Harborline Auto LLC

Car Dealer Customer Service
Address: 2874 Cresthaven Road, Shelbyville, TN 37162
web: www.harborlineautoxq.net
email: harborlineautoxq@mailnest.example
Phone: (931) 555-0148
Phone: (629) 555-0173

```html
<!DOCTYPE html>
<html lang="en">
<head>
<meta charset="utf-8">
<title>Harborline Auto – Business Card</title>
<link rel="stylesheet" href="https://fonts.googleapis.com/css2?family=Poppins:wght@400;600;700&family=Oswald:wght@700&display=swap">
<style>
  :root {
    --bg: #2a2a2a;
    --card: #f1f1f0;
    --blue: #1e78aa;
    --gold: #dca739;
    --ink: #1d1d1d;
    --white: #ffffff;
  }
  * { margin: 0; padding: 0; box-sizing: border-box; }
  html, body { width: 1200px; height: 1138px; overflow: hidden; }
  body { background: var(--bg); font-family: "Poppins", sans-serif; position: relative; }

  .card {
    position: absolute;
    width: 620px;
    height: 374px;
    border-radius: 16px;
    background: var(--card);
    overflow: hidden;
  }
  .card--front { left: 274px; top: 186px; }
  .card--back  { left: 276px; top: 608px; }

  .brand {
    position: absolute;
    display: flex;
    align-items: center;
    gap: 12px;
    font-family: "Poppins", sans-serif;
    font-weight: 700;
    color: var(--blue);
    letter-spacing: 0.5px;
    white-space: nowrap;
    line-height: 1;
  }
  .brand__dot {
    width: 22px; height: 22px; border-radius: 50%;
    background: var(--gold);
    flex: none;
  }
  .card--front .brand { left: 0; right: 0; top: 220px; justify-content: center; font-size: 30px; }

  .front-web {
    position: absolute; left: 0; right: 0; top: 320px;
    display: flex; align-items: center; justify-content: center; gap: 26px;
    font-size: 15px; color: var(--ink);
  }
  .front-web__rule { width: 56px; height: 2px; background: var(--gold); }

  .front-bands { position: absolute; left: 0; right: 0; bottom: 0; height: 18px; display: flex; }
  .front-bands__blue { flex: 1; background: var(--blue); }
  .front-bands__gold { flex: 1; background: var(--gold); }

  .phones { position: absolute; left: 30px; top: 62px; }
  .phones__row {
    display: flex; align-items: center; gap: 14px;
    font-family: "Oswald", sans-serif; font-weight: 700;
    font-size: 27px; line-height: 29px; color: var(--ink);
  }
  .phones__icon { width: 20px; height: 20px; flex: none; }

  .card--back .brand { left: 330px; top: 212px; font-size: 24px; }
  .card--back .brand__dot { width: 18px; height: 18px; }

  .wave { position: absolute; left: 0; top: 0; width: 620px; height: 374px; }

  .contact {
    position: absolute; left: 30px; top: 262px;
    color: var(--white); font-size: 15px; line-height: 21px;
  }
  .contact__address { margin-bottom: 10px; }
  .contact__row { display: flex; align-items: center; gap: 10px; }
  .contact__icon { width: 12px; height: 12px; flex: none; }
</style>
</head>
<body>

<section class="card card--front" aria-label="Card front">
  <div class="brand"><span class="brand__dot"></span>HARBORLINE AUTO</div>
  <div class="front-web">
    <span class="front-web__rule"></span>
    <span>www.harborlineautoxq.net</span>
    <span class="front-web__rule"></span>
  </div>
  <div class="front-bands">
    <span class="front-bands__blue"></span>
    <span class="front-bands__gold"></span>
  </div>
</section>

<section class="card card--back" aria-label="Card back">
  <svg class="wave" viewBox="0 0 620 374" aria-hidden="true">
    <path d="M0 210 C70 190 140 186 200 194 C260 204 300 236 360 262 C440 296 540 318 620 298 L620 374 L0 374 Z" fill="var(--gold)"/>
    <path d="M0 218 C70 198 140 194 200 202 C260 212 300 244 360 270 C440 304 540 326 620 306 L620 374 L0 374 Z" fill="var(--card)"/>
    <path d="M0 230 C70 212 140 210 200 220 C260 230 300 258 360 282 C440 316 540 338 620 318 L620 374 L0 374 Z" fill="var(--blue)"/>
  </svg>

  <div class="phones">
    <div class="phones__row">
      <svg class="phones__icon" viewBox="0 0 20 20" aria-hidden="true"><path d="M5 1h3l1.5 4-2 1.5a11 11 0 0 0 6 6l1.5-2 4 1.5v3a2 2 0 0 1-2 2A17 17 0 0 1 3 3a2 2 0 0 1 2-2z" fill="var(--gold)"/></svg>
      <span>931-555-0148</span>
    </div>
    <div class="phones__row">
      <svg class="phones__icon" viewBox="0 0 20 20" aria-hidden="true"><path d="M5 1h3l1.5 4-2 1.5a11 11 0 0 0 6 6l1.5-2 4 1.5v3a2 2 0 0 1-2 2A17 17 0 0 1 3 3a2 2 0 0 1 2-2z" fill="var(--gold)"/></svg>
      <span>629-555-0173</span>
    </div>
  </div>

  <div class="brand"><span class="brand__dot"></span>HARBORLINE AUTO</div>

  <div class="contact">
    <p class="contact__address">2874 Cresthaven Road,<br>Shelbyville, TN 37162</p>
    <p class="contact__row">
      <svg class="contact__icon" viewBox="0 0 12 12" aria-hidden="true"><rect x="0.5" y="2" width="11" height="8" fill="var(--gold)"/><path d="M0.5 2 6 7 11.5 2" fill="none" stroke="var(--blue)" stroke-width="1"/></svg>
      <span>www.harborlineautoxq.net</span>
    </p>
    <p class="contact__row">
      <svg class="contact__icon" viewBox="0 0 12 12" aria-hidden="true"><circle cx="6" cy="6" r="5.5" fill="var(--gold)"/><path d="M0.5 6h11M6 0.5c-3 3-3 8 0 11M6 0.5c3 3 3 8 0 11" fill="none" stroke="var(--blue)" stroke-width="0.8"/></svg>
      <span>harborlineautoxq@mailnest.example</span>
    </p>
  </div>
</section>

</body>
</html>
```